Maple Bus Card

i own a building in the bronx ny - its called "Maple 7 on 2 HDFC"i want a classy logo / business card - nothing too religuous but it is like a family there - its a large apartment building - colors i like dark red, black, medium shade of gray also reg business card stuff tel # 914-555-0173 address 4738 Larkwell Ave Bronx NY 10460 Email fijosh@aol.comslogan - " from many we are one "i can send u a picture of the building for the backside

```html
<!DOCTYPE html>
<html lang="en">
<head>
<meta charset="utf-8">
<title>Maple 7 on 2 HDFC – Business Card</title>
<link href="https://fonts.googleapis.com/css2?family=Open+Sans:wght@400;600;700&family=Oswald:wght@500&display=swap" rel="stylesheet">
<style>
  :root {
    --backdrop: #8a8a8a;
    --card-white: #efefef;
    --card-black: #151515;
    --brand-red: #d20c0c;
    --ink: #2b2b2b;
    --rule: #555555;
  }
  * { box-sizing: border-box; margin: 0; padding: 0; }
  html, body {
    width: 1200px; height: 1200px; overflow: hidden;
    background: var(--backdrop);
  }
  .canvas { position: relative; width: 1200px; height: 1200px; }
  .card {
    position: absolute; top: 310px;
    width: 366px; height: 594px;
    box-shadow: 2px 3px 6px rgba(0,0,0,0.45);
    overflow: hidden;
  }
  .card-front {
    left: 234px; background: var(--card-white);
    font-family: "Open Sans", Arial, sans-serif; text-align: center; color: var(--ink);
  }
  .card-back { left: 629px; background: var(--card-black); }

  .brand-name {
    position: absolute; top: 226px; left: 0; right: 0;
    font-weight: 700; font-size: 32px; letter-spacing: -0.5px;
    color: var(--brand-red);
  }
  .contact { position: absolute; top: 372px; left: 0; right: 0; }
  .person-name { font-weight: 600; font-size: 19px; color: var(--brand-red); line-height: 24px; }
  .person-title { font-size: 17px; line-height: 22px; }
  .divider { width: 132px; height: 1px; background: var(--rule); margin: 9px auto 10px; }
  .detail { font-size: 17px; line-height: 22px; }

  .slogan {
    position: absolute; top: 130px; left: 0; right: 0; text-align: center;
    font-family: "Oswald", "Arial Narrow", sans-serif; font-weight: 500;
    font-size: 66px; line-height: 74px; color: var(--brand-red);
    letter-spacing: -1px;
  }
  .base-band { position: absolute; left: 0; bottom: 0; }
</style>
</head>
<body>
<main class="canvas">
  <section class="card card-front">
    <div class="brand-name">Maple 7 on 2 HDFC</div>
    <div class="contact">
      <p class="person-name">DANIEL REYES</p>
      <p class="person-title">Managing Director</p>
      <div class="divider"></div>
      <p class="detail">914-555-0173</p>
      <p class="detail">mavreld@quintmail.com</p>
      <div class="divider"></div>
      <p class="detail">4738 Larkwell Ave</p>
      <p class="detail">Fennmore NY 10977</p>
    </div>
  </section>

  <section class="card card-back">
    <p class="slogan">From many<br>we are one</p>
    <svg class="base-band" width="366" height="120" viewBox="0 0 366 120" aria-hidden="true">
      <path d="M0 42 Q183 130 366 42 L366 120 L0 120 Z" fill="var(--brand-red)"/>
    </svg>
  </section>
</main>
</body>
</html>
```